Elegant Business Card for Technology Company

Client is a supplier of innovative industrial communications and automation equipment since 2002. This contest is to gather fresh ideas for a redesign of the existing business card. Client is looking for design that best communicates tagline "Industrial Networking and Computing Specialist".

Design submissions should look modern, clean, elegant and professional. It should not be cluttered. Use white as the primary colour. Orange and black as secondary colour. Refer to jpeg File 1 on the current design.

Fonts used by Client used include Arial Regular, Arial Black, Roboto Regular, Roboto Black and Lato.

The winning design will be sent for offset printing using super white 250gsm artcard paper (open for suggestions).

Target Market(s)

System Engineers, Project Managers, Purchasing Managers from companies providing engineering services for Smart Cities.

Industry/Entity Type

Information Technology

Contact Information for Business Card

Refer to PDF File 3 for Business Card Details. Priority of short contact information would be as follows Name > Job Title > Email > Mobile > Web > Tel > Fax > Business Address >UEN (UEN represents company registration number)

Font styles to use
Sans Serif

Colors
ffffff
f37122
000000
5c5c5c

Requirements
Must have
• Refer to AI File 2 (Company Logo) & PDF File 3 (Information on Namecard)
Should not have
• No QR codes
• No Social Media Icons
• Do not create full Black or Orange colour background

```html
<!DOCTYPE html>
<html lang="en">
<head>
<meta charset="utf-8">
<title>KVR Asia Pacific Business Card</title>
<link href="https://fonts.googleapis.com/css2?family=Roboto:wght@400;500;700;900&display=swap" rel="stylesheet">
<style>
  :root {
    --orange: #f37122;
    --black: #000000;
    --white: #ffffff;
    --grey: #5c5c5c;
    --ink: #1a1a1a;
    --backdrop: #d4d4d4;
  }
  * { margin: 0; padding: 0; box-sizing: border-box; }
  html, body { width: 1200px; height: 900px; overflow: hidden; }
  body {
    background: var(--backdrop);
    font-family: "Roboto", Arial, sans-serif;
    display: flex;
    align-items: center;
    justify-content: center;
    gap: 40px;
  }
  .card {
    position: relative;
    width: 540px;
    height: 310px;
    background: var(--white);
    overflow: hidden;
    box-shadow: 0 10px 28px rgba(0,0,0,0.22);
  }
  .card-bands { position: absolute; inset: 0; width: 100%; height: 100%; }
  .brand {
    display: flex;
    align-items: center;
    gap: 12px;
  }
  .brand-dot {
    width: 58px; height: 58px;
    border-radius: 50%;
    background: var(--orange);
  }
  .brand-name {
    font-weight: 900;
    font-size: 58px;
    color: var(--grey);
    letter-spacing: 2px;
    line-height: 1;
  }
  /* front */
  .front-content {
    position: absolute;
    inset: 0;
    display: flex;
    flex-direction: column;
    align-items: center;
    justify-content: center;
    padding-top: 4px;
  }
  .tagline {
    margin-top: 14px;
    color: var(--orange);
    font-size: 13px;
    font-weight: 700;
    letter-spacing: 0.2px;
    text-transform: uppercase;
  }
  .services {
    list-style: none;
    margin-top: 8px;
    text-align: center;
    color: var(--ink);
    font-size: 13px;
    line-height: 1.35;
  }
  /* back */
  .back-brand {
    position: absolute;
    right: 40px;
    top: 70px;
    display: flex;
    flex-direction: column;
    align-items: flex-start;
  }
  .company-name {
    margin-top: 12px;
    color: var(--ink);
    font-size: 14px;
    font-weight: 500;
    letter-spacing: 0.3px;
  }
  .company-name .accent { color: var(--orange); font-weight: 700; }
  .contact {
    position: absolute;
    left: 28px;
    top: 100px;
    color: var(--ink);
  }
  .person-name {
    color: var(--orange);
    font-weight: 900;
    font-size: 19px;
    letter-spacing: 0.4px;
  }
  .job-title { font-size: 12px; font-weight: 700; letter-spacing: 0.4px; margin-top: 1px; }
  .address { font-size: 12px; line-height: 1.35; margin-top: 6px; color: var(--grey); }
  .contact-list { list-style: none; margin-top: 6px; }
  .contact-item {
    display: flex;
    align-items: center;
    gap: 9px;
    font-size: 12.5px;
    line-height: 1.5;
  }
  .contact-icon { width: 11px; height: 11px; flex: none; }
  .uen {
    position: absolute;
    left: 28px;
    bottom: 9px;
    color: var(--white);
    font-size: 13px;
    font-weight: 700;
    letter-spacing: 0.3px;
  }
</style>
</head>
<body>

  <section class="card card-front" aria-label="Business card front">
    <svg class="card-bands" viewBox="0 0 540 310" preserveAspectRatio="none" aria-hidden="true">
      <polygon points="0,0 540,0 540,14 250,14 222,46 0,46" fill="var(--orange)"/>
      <polygon points="250,14 222,46 232,46 260,14" fill="var(--black)"/>
      <polygon points="540,310 0,310 0,296 290,296 318,264 540,264" fill="var(--orange)"/>
      <polygon points="290,296 318,264 308,264 280,296" fill="var(--black)"/>
    </svg>
    <div class="front-content">
      <div class="brand">
        <span class="brand-dot"></span>
        <span class="brand-name">KVR</span>
      </div>
      <p class="tagline">Industrial Networking and Computing Specialist</p>
      <ul class="services">
        <li>Industrial Ethernet / Wireless / Cellular</li>
        <li>Industrial and Embedded Computing</li>
        <li>Serial / Fieldbus Connectivity</li>
        <li>IP Video Surveillance</li>
        <li>Remote Automation</li>
      </ul>
    </div>
  </section>

  <section class="card card-back" aria-label="Business card back">
    <svg class="card-bands" viewBox="0 0 540 310" preserveAspectRatio="none" aria-hidden="true">
      <polygon points="0,0 540,0 540,14 300,14 272,46 0,46" fill="var(--orange)"/>
      <polygon points="300,14 272,46 282,46 310,14" fill="var(--black)"/>
      <polygon points="0,310 540,310 540,244 340,244 312,276 0,276" fill="var(--orange)"/>
      <polygon points="340,244 312,276 302,276 330,244" fill="var(--black)"/>
    </svg>

    <div class="back-brand">
      <div class="brand">
        <span class="brand-dot"></span>
        <span class="brand-name">KVR</span>
      </div>
      <p class="company-name"><span class="accent">KVR</span> ASIA PACIFIC PTE LTD</p>
    </div>

    <div class="contact">
      <p class="person-name">DANIEL KOH</p>
      <p class="job-title">SALES MANAGER</p>
      <p class="address">22 Kallang Way Link Hub #05-12<br>(Block B), Singapore 349287</p>
      <ul class="contact-list">
        <li class="contact-item">
          <svg class="contact-icon" viewBox="0 0 12 12"><rect x="3" y="0.5" width="6" height="11" rx="1.2" fill="none" stroke="var(--orange)" stroke-width="1.3"/><circle cx="6" cy="9.4" r="0.8" fill="var(--orange)"/></svg>
          <span>+65 9123 4567</span>
        </li>
        <li class="contact-item">
          <svg class="contact-icon" viewBox="0 0 12 12"><path d="M2.5 1 L4.6 1 L5.4 3.6 L4 4.6 C4.8 6.3 5.7 7.2 7.4 8 L8.4 6.6 L11 7.4 L11 9.5 C11 10.4 10.3 11 9.4 11 C5 10.6 1.4 7 1 2.6 C1 1.7 1.6 1 2.5 1 Z" fill="var(--orange)"/></svg>
          <span>+65 6234 5810</span>
        </li>
        <li class="contact-item">
          <svg class="contact-icon" viewBox="0 0 12 12"><rect x="2.5" y="0.5" width="7" height="4" fill="var(--orange)"/><rect x="0.5" y="4.5" width="11" height="5" rx="1" fill="var(--orange)"/><rect x="2.5" y="8" width="7" height="3.5" fill="var(--orange)"/></svg>
          <span>+65 6234 5811</span>
        </li>
        <li class="contact-item">
          <svg class="contact-icon" viewBox="0 0 12 12"><rect x="0.8" y="2.2" width="10.4" height="7.6" fill="none" stroke="var(--orange)" stroke-width="1.2"/><polyline points="0.8,2.4 6,6.6 11.2,2.4" fill="none" stroke="var(--orange)" stroke-width="1.2"/></svg>
          <span>sales@kvr-ap.sg</span>
        </li>
        <li class="contact-item">
          <svg class="contact-icon" viewBox="0 0 12 12"><circle cx="6" cy="6" r="5.2" fill="none" stroke="var(--orange)" stroke-width="1.1"/><ellipse cx="6" cy="6" rx="2.2" ry="5.2" fill="none" stroke="var(--orange)" stroke-width="1"/><line x1="0.8" y1="6" x2="11.2" y2="6" stroke="var(--orange)" stroke-width="1"/></svg>
          <span>www.kvr-ap.sg</span>
        </li>
      </ul>
    </div>

    <p class="uen">UEN No: 200315472K</p>
  </section>

</body>
</html>
```